New iOS App design for Boston Startup

We are looking for a new app design for our iPhone app. The current app's design feels outdated and we like to add lots of new functionality and a new navigation as well. A complete overhaul therefore!
We want you to design 5 screens that will have changed the most. The complete wireframes of these 5 pages are attached in the requirements document.
Once the winning design is selected we will award the winner with the designing all other screens (40-50 screens based on the same design). This will be a separate project worth $1000. The winning designer can get more follow up work if both sides are happy about the cooperation.
We will give feedback as soon as the first screen has been uploaded for review. Final decision will be made only after all 5 screens are finished.
We hope you give it your best!
Note: will only communicate through PixelHarbor (no skype),
Updates
Reason: Want to give designers a chance to submit their designs as I understand from some, the deadline is too close.
I have raised the award and introduced a 2nd price as well to make it worth your time. I hope you give it your best shot.
Reason: A few of you have asked for an extension of the deadline as time is running out. I will extend by one day. Tell me if you need more.
Industry/Entity Type
Startup
Requirements
Must have
- At least 1 screen before we can give you feedback.
Nice to have
- multiple options of 1 screen to get to a desirable design

```html
<!DOCTYPE html>
<html lang="en">
<head>
<meta charset="utf-8">
<title>Practice-SC</title>
<link rel="stylesheet" href="https://fonts.googleapis.com/css2?family=Roboto:wght@400;500;700&display=swap">
<style>
  :root {
    --navy: #0e3a5b;
    --navy-dark: #0a2e49;
    --cyan: #19b2e6;
    --page: #e6e7e8;
    --card: #ffffff;
    --green: #3f7a1a;
    --orange: #f5a21c;
    --track: #d9d9d9;
    --ink: #1a1a1a;
    --muted: #a8a8a8;
    --white: #ffffff;
  }
  * { box-sizing: border-box; margin: 0; padding: 0; }
  html, body { width: 847px; height: 1200px; overflow: hidden; }
  body { font-family: "Roboto", "Helvetica Neue", Arial, sans-serif; background: var(--page); position: relative; }

  .top-bar { position: absolute; left: 0; top: 0; width: 847px; height: 180px; background: var(--navy); color: var(--white); }
  .status-bar { height: 58px; display: flex; align-items: center; justify-content: space-between; padding: 0 22px; font-size: 26px; font-weight: 500; }
  .status-left, .status-right { display: flex; align-items: center; gap: 12px; width: 260px; }
  .status-right { justify-content: flex-end; }
  .status-time { font-weight: 700; }
  .battery { width: 52px; height: 24px; border: 2px solid var(--white); border-radius: 4px; padding: 2px; }
  .battery span { display: block; width: 100%; height: 100%; background: var(--white); border-radius: 1px; }

  .nav-bar { height: 122px; display: flex; align-items: center; justify-content: center; position: relative; }
  .nav-back { position: absolute; left: 26px; top: 50%; transform: translateY(-50%); display: flex; align-items: center; gap: 14px; font-size: 42px; font-weight: 500; }
  .nav-title { font-size: 46px; font-weight: 700; }

  .lesson-list { position: absolute; left: 15px; right: 15px; top: 202px; list-style: none; }
  .lesson-card { height: 126px; margin-bottom: 27px; background: var(--card); border-radius: 6px; position: relative; overflow: hidden; box-shadow: 0 1px 2px rgba(0,0,0,.08); }
  .lesson-card::before { content: ""; position: absolute; left: 0; top: 0; right: 0; height: 8px; background: var(--green); }
  .lesson-card.in-progress::before { background: linear-gradient(to right, var(--orange) 0 50%, var(--track) 50% 100%); }
  .lesson-body { position: absolute; left: 28px; top: 24px; }
  .lesson-number { font-size: 26px; color: var(--muted); }
  .lesson-name { font-size: 38px; color: var(--ink); margin-top: 2px; }
  .in-progress .lesson-number { color: var(--ink); font-weight: 700; }
  .chevron { position: absolute; right: 26px; top: 50%; transform: translateY(-40%); }

  .tab-bar { position: absolute; left: 0; bottom: 0; width: 847px; height: 132px; background: var(--navy); display: flex; }
  .tab { flex: 1; display: flex; flex-direction: column; align-items: center; justify-content: flex-end; padding-bottom: 12px; color: var(--white); font-size: 27px; font-weight: 700; gap: 10px; }
  .tab.active { background: var(--cyan); margin-top: -14px; }
</style>
</head>
<body>
  <header class="top-bar">
    <div class="status-bar">
      <div class="status-left">
        <span>●●○○○</span><span>Lumo</span>
        <svg width="30" height="22" viewBox="0 0 30 22"><path d="M2 8a19 19 0 0 1 26 0M7 13a12 12 0 0 1 16 0M12 18a5 5 0 0 1 6 0" fill="none" stroke="#fff" stroke-width="3" stroke-linecap="round"/></svg>
      </div>
      <div class="status-time">23:12</div>
      <div class="status-right">
        <svg width="16" height="26" viewBox="0 0 16 26"><path d="M2 7l12 12-6 5V2l6 5L2 19" fill="none" stroke="#fff" stroke-width="2.5"/></svg>
        <span>100%</span>
        <div class="battery"><span></span></div>
      </div>
    </div>
    <nav class="nav-bar">
      <div class="nav-back">
        <svg width="22" height="38" viewBox="0 0 22 38"><path d="M19 3L4 19l15 16" fill="none" stroke="#fff" stroke-width="5" stroke-linecap="round" stroke-linejoin="round"/></svg>
        <span>Back</span>
      </div>
      <h1 class="nav-title">Practice-SC</h1>
    </nav>
  </header>

  <ul class="lesson-list">
    <li class="lesson-card"><div class="lesson-body"><div class="lesson-number">Lesson 1</div><div class="lesson-name">Sentence Correction</div></div>
      <svg class="chevron" width="18" height="30" viewBox="0 0 18 30"><path d="M3 3l12 12L3 27" fill="none" stroke="#1a1a1a" stroke-width="4"/></svg></li>
    <li class="lesson-card"><div class="lesson-body"><div class="lesson-number">Lesson 1</div><div class="lesson-name">Grammar Correction</div></div>
      <svg class="chevron" width="18" height="30" viewBox="0 0 18 30"><path d="M3 3l12 12L3 27" fill="none" stroke="#1a1a1a" stroke-width="4"/></svg></li>
    <li class="lesson-card"><div class="lesson-body"><div class="lesson-number">Lesson 2</div><div class="lesson-name">Language Translation</div></div>
      <svg class="chevron" width="18" height="30" viewBox="0 0 18 30"><path d="M3 3l12 12L3 27" fill="none" stroke="#1a1a1a" stroke-width="4"/></svg></li>
    <li class="lesson-card in-progress"><div class="lesson-body"><div class="lesson-number">Lesson 3</div><div class="lesson-name">Essay Writing</div></div>
      <svg class="chevron" width="18" height="30" viewBox="0 0 18 30"><path d="M3 3l12 12L3 27" fill="none" stroke="#1a1a1a" stroke-width="4"/></svg></li>
  </ul>

  <nav class="tab-bar">
    <div class="tab">
      <svg width="44" height="54" viewBox="0 0 44 54"><rect x="4" y="3" width="36" height="48" rx="3" fill="none" stroke="#fff" stroke-width="3"/><line x1="10" y1="3" x2="10" y2="51" stroke="#fff" stroke-width="3"/></svg>
      <span>Theory</span>
    </div>
    <div class="tab">
      <svg width="50" height="54" viewBox="0 0 50 54"><path d="M36 4l10 10L16 44 4 50l6-12z M32 8l10 10" fill="none" stroke="#fff" stroke-width="3" stroke-linejoin="round"/></svg>
      <span>Practice</span>
    </div>
    <div class="tab active">
      <svg width="62" height="56" viewBox="0 0 62 56"><path d="M31 3L3 28h8v25h15V37h10v16h15V28h8z" fill="#fff"/></svg>
      <span>Home</span>
    </div>
    <div class="tab">
      <svg width="50" height="54" viewBox="0 0 50 54"><circle cx="25" cy="10" r="7" fill="none" stroke="#fff" stroke-width="3"/><line x1="25" y1="17" x2="25" y2="36" stroke="#fff" stroke-width="3"/><path d="M6 40h38v10H6z" fill="none" stroke="#fff" stroke-width="3"/></svg>
      <span>Games</span>
    </div>
    <div class="tab">
      <svg width="44" height="54" viewBox="0 0 44 54"><path d="M4 3h26l10 10v38H4z" fill="none" stroke="#fff" stroke-width="3" stroke-linejoin="round"/><path d="M11 20h22M11 28h22M11 36h22M11 44h14" stroke="#fff" stroke-width="3"/></svg>
      <span>Test</span>
    </div>
  </nav>
</body>
</html>
```